Sell the dream! Property investment proposal document

We are looking for a proposal document which outlines our vision for property development. The purpose of the document is to raise investment from investors - sell the dream!
Brief summary:
Kestrel Dwellings Developments, is an emerging New Zealand property investment company with a focus on providing unique property investment opportunities.
Our expertise and capabilities in architectural modular homes provide us with a remarkable advantage in tackling the development of properties that are typically considered challenging, remote, or uniquely positioned.
Our specialization in this niche sector of property development not only sets us apart from competitors, but also paves the way for lucrative investment opportunities in the New Zealand property market.
Feel free to use any images from www.kestreldwellings.co.nz
Target Market(s)
investors for a unique property development opportunity
Industry/Entity Type
luxury property development in unique locations throughout New Zealand
Colors
Designer to choose only greyscale colors for use in the design.
Look and feel

```html
<!DOCTYPE html>
<html lang="en">
<head>
<meta charset="utf-8">
<title>Kestrel Dwellings Developments – Investment Proposal</title>
<link rel="stylesheet" href="https://fonts.googleapis.com/css2?family=Archivo:wght@300;400;600;700&display=swap">
<style>
  :root {
    --canvas: #e8e8e7;
    --page: #131313;
    --page-deep: #0b0b0b;
    --ink: #f2f2f2;
    --ink-soft: #d0d0d0;
    --dot-on: #dcdcdc;
    --dot-mid: #a8a8a8;
    --dot-off: #555555;
  }
  * { box-sizing: border-box; margin: 0; padding: 0; }
  html, body { width: 896px; height: 1200px; overflow: hidden; }
  body {
    background: var(--canvas);
    font-family: "Archivo", Arial, sans-serif;
    color: var(--ink);
    position: relative;
  }
  .spread {
    position: absolute;
    left: 78px;
    width: 752px;
    height: 294px;
    display: flex;
    box-shadow: 0 4px 14px rgba(0,0,0,0.18);
  }
  .spread--finance { top: 151px; }
  .spread--about { top: 751px; }
  .page {
    position: relative;
    width: 376px;
    height: 294px;
    background: var(--page);
    overflow: hidden;
  }
  .page--left { background: linear-gradient(90deg, var(--page) 88%, var(--page-deep)); }
  .page--right { background: linear-gradient(90deg, var(--page-deep), var(--page) 10%); }
  .photo { position: absolute; }

  .section-title {
    position: absolute;
    font-size: 12.5px;
    line-height: 1;
    font-weight: 300;
    color: var(--ink);
    white-space: nowrap;
  }
  .section-title strong { font-weight: 700; }
  .section-title--wide { font-weight: 500; letter-spacing: 0.26em; font-size: 12px; }
  .dots { position: absolute; display: flex; gap: 5px; }
  .dots span { width: 4px; height: 4px; border-radius: 50%; background: var(--dot-on); }
  .dots span:nth-child(3) { background: var(--dot-mid); }
  .dots span:last-child { background: var(--dot-off); }
  .body-copy {
    position: absolute;
    font-size: 5px;
    line-height: 7.9px;
    color: var(--ink-soft);
  }
  .body-copy p + p { margin-top: 8px; }

  .wordmark {
    position: absolute;
    left: 20px;
    bottom: 18px;
    writing-mode: vertical-rl;
    transform: rotate(180deg);
    font-size: 42px;
    line-height: 1;
    font-weight: 300;
    color: var(--ink);
    white-space: nowrap;
  }
</style>
</head>
<body>

<section class="spread spread--finance">
  <div class="page page--left">
    <div class="photo" role="img" aria-label="Dark-clad modular home with glass sliders, garden and palms under a blue sky"
         style="left:0;top:0;width:376px;height:213px;background:linear-gradient(180deg,#c4d0db 0%,#aab6c0 22%,#4a4a44 40%,#2e2e2b 62%,#8a8c86 74%,#4f5e3a 86%,#6b7d45 100%);"></div>
    <div class="photo" role="img" aria-label="Kitchen interior with timber joinery and dark island"
         style="left:8px;top:220px;width:120px;height:69px;background:linear-gradient(180deg,#e6e6e4 0%,#9a8468 40%,#2a2a2a 75%,#5a5a5a 100%);"></div>
    <div class="photo" role="img" aria-label="Bedroom with full-height glazing and soft light"
         style="left:135px;top:220px;width:118px;height:69px;background:linear-gradient(90deg,#c9b48e 0%,#8a9480 35%,#4a4640 60%,#bdb6aa 85%,#6b6258 100%);"></div>
    <div class="photo" role="img" aria-label="Dining room with dark table and sheer curtains"
         style="left:260px;top:220px;width:111px;height:69px;background:linear-gradient(90deg,#e8eaec 0%,#b8bcbf 30%,#2c2c2c 55%,#9c8a70 70%,#d9dcdf 100%);"></div>
  </div>
  <div class="page page--right">
    <h2 class="section-title" style="left:35px;top:51px;">FINANCIAL <strong>SUMMARY</strong></h2>
    <div class="dots" style="left:35px;top:80px;"><span></span><span></span><span></span><span></span></div>
    <div class="body-copy" style="left:35px;top:111px;width:160px;">
      <p>In terms of financial projections, with each development, we anticipate a profit of 10%-20% which will be project dependent.</p>
      <p>This growth is fueled by the increasing demand for unique property investments in New Zealand and our ability to deliver high-quality services to the market in a condensed time frame, with heavily controlled costs.</p>
      <p>With a solid business model and a dedicated team, we are confident in our ability to achieve success and establish Kestrel Dwellings Investments as a trusted name in the industry.</p>
    </div>
    <div class="body-copy" style="left:221px;top:112px;width:136px;">
      <p>New Zealand's property market has been experiencing steady growth over the years, making it an attractive destination for property investors. With its beautiful landscapes and strong economy, New Zealand offers a diverse range of investment opportunities for both local and international investors. The demand for quality properties in prime locations continues to rise, creating a favorable environment for property investment companies like ours that can lean on our modular benefits of being able to reach unique and remote locations.</p>
    </div>
    <div class="photo" role="img" aria-label="Long low modular home at dusk with lit windows and lawn"
         style="left:0;top:213px;width:376px;height:81px;background:linear-gradient(180deg,#d6d6d2 0%,#b8bcbc 30%,#2a2b2c 48%,#3a3a38 68%,#7a7c70 78%,#4c5c36 90%,#5d6e40 100%);"></div>
  </div>
</section>

<section class="spread spread--about">
  <div class="page page--left">
    <div class="wordmark">Kestrel</div>
    <h2 class="section-title section-title--wide" style="left:88px;top:53px;">ABOUT US</h2>
    <div class="dots" style="left:88px;top:83px;"><span></span><span></span><span></span><span></span></div>
    <div class="body-copy" style="left:88px;top:111px;width:118px;">
      <p>We produce and deliver architecturally-designed, highly customisable homes, built off-site, delivered to and assembled on your own, personal plot of land anywhere in New Zealand.</p>
      <p>At Kestrel, our aim is to help people envision their own homes; to simplify the process of crafting and building them to exacting standards; and give our customers and their families personalised homes in which to forge memories of shelter and comfort. Kestrel: Modular, architectural homes with flexibility and sophistication.</p>
      <p>Customisation is at the heart of what we do here at Kestrel so that your home can best take advantage of its site and reflect you and your family's lifestyle. If you can imagine it, we can make it happen.</p>
    </div>
    <div class="photo" role="img" aria-label="Open-plan living room with timber ceiling, skylights and sea view"
         style="left:230px;top:0;width:127px;height:140px;background:linear-gradient(180deg,#b0916c 0%,#8a7258 22%,#dfe3e6 38%,#a9b0b4 52%,#6e6a66 70%,#3a3634 100%);"></div>
    <div class="photo" role="img" aria-label="Two-storey dark-clad home with concrete base and driveway"
         style="left:230px;top:154px;width:127px;height:140px;background:linear-gradient(180deg,#d2d8de 0%,#aeb5bb 30%,#2a2c2d 50%,#3c3e3d 70%,#b3b3b0 85%,#d0d0ce 100%);"></div>
  </div>
  <div class="page page--right">
    <div class="photo" role="img" aria-label="Black and white portrait of the two founders seated together"
         style="left:17px;top:45px;width:87px;height:118px;background:linear-gradient(180deg,#f2f2f2 0%,#d4d4d4 35%,#3a3a3a 60%,#262626 85%,#bcbcbc 100%);"></div>
    <h2 class="section-title section-title--wide" style="left:133px;top:51px;">OUR FOUNDERS</h2>
    <div class="dots" style="left:133px;top:80px;"><span></span><span></span><span></span><span></span></div>
    <div class="body-copy" style="left:133px;top:111px;width:208px;">
      <p>After finding the perfect piece of land, Liam and Tessa went on a quest to build their first family home: a stylish, customisable, architectural, and high quality abode that was also cost-effective. With no success, the ideas started flowing: What if New Zealand had access to modern, high quality, prefabricated homes? It was with this simple premise of design and construction excellence at fair prices that allowed Kestrel to be born.</p>
      <p>Since then, the business has grown to over 40 people, and will soon be shifting to a custom-built factory in Kumeu, Auckland in early 2023, whilst retaining the positive work-culture and family-driven goals that motivated them in the first place.</p>
    </div>
    <div class="photo" role="img" aria-label="White line rendering of a modular home elevation"
         style="left:7px;top:212px;width:369px;height:70px;background:linear-gradient(180deg,rgba(200,200,200,0.05) 0%,rgba(200,200,200,0.35) 20%,rgba(170,170,170,0.45) 60%,rgba(120,120,120,0.25) 85%,rgba(60,60,60,0.05) 100%);"></div>
  </div>
</section>

</body>
</html>
```